Business card design for Quorvel Engineering Tandem

We need a new business card design along with all the necessary to place an order. The company is Quorvel Engineering Tandem and we recently updated our logo.

```html
<!DOCTYPE html>
<html lang="en">
<head>
<meta charset="utf-8">
<title>Quorvel Engineering Tandem — Business Card</title>
<link href="https://fonts.googleapis.com/css2?family=Montserrat:wght@400;500;700;800&display=swap" rel="stylesheet">
<style>
  :root {
    --backdrop: #1c1c1e;
    --gold: #e1bd24;
    --gold-light: #f0d65a;
    --gold-text: #e0b31c;
    --paper: #ffffff;
    --steel: #9a9a9a;
    --ink: #1a1a1a;
  }
  * { margin: 0; padding: 0; box-sizing: border-box; }
  html, body {
    width: 1200px; height: 874px; overflow: hidden;
    background: var(--backdrop);
    font-family: "Montserrat", sans-serif;
  }
  .canvas {
    width: 1200px; height: 874px;
    display: flex; flex-direction: column;
    align-items: center; justify-content: center; gap: 40px;
  }
  .card {
    width: 620px; height: 354px;
    border-radius: 26px;
    position: relative;
    overflow: hidden;
  }
  .card--front {
    background: var(--gold);
    display: flex; align-items: center; justify-content: center;
  }
  .brand {
    display: flex; align-items: center; gap: 12px;
    font-weight: 800; text-transform: uppercase; letter-spacing: 0.5px;
    white-space: nowrap;
  }
  .brand__mark { width: 20px; height: 20px; flex: none; }
  .card--front .brand { color: var(--gold-light); font-size: 26px; }
  .card--front .brand__mark { background: var(--gold-light); }
  .card--back { background: var(--paper); }
  .card--back .brand {
    position: absolute; left: 0; right: 0; top: 88px;
    justify-content: center;
    color: var(--steel); font-size: 26px;
  }
  .card--back .brand__mark { background: var(--gold); }
  .identity {
    position: absolute; right: 356px; top: 230px;
    text-align: right;
  }
  .identity__name {
    color: var(--gold-text); font-weight: 700; font-size: 23px; line-height: 1.1;
    white-space: nowrap;
  }
  .identity__role {
    color: var(--ink); font-weight: 500; font-size: 14px; margin-top: 4px;
    white-space: nowrap;
  }
  .divider {
    position: absolute; left: 280px; top: 228px;
    width: 1.5px; height: 82px; background: var(--gold);
  }
  .contacts {
    position: absolute; left: 298px; top: 232px;
    list-style: none;
    display: flex; flex-direction: column; gap: 9px;
  }
  .contacts__item {
    display: flex; align-items: center; gap: 10px;
    color: var(--ink); font-size: 14px; font-weight: 500;
    white-space: nowrap;
  }
  .contacts__icon { width: 13px; height: 13px; flex: none; }
</style>
</head>
<body>
<main class="canvas">
  <section class="card card--front">
    <div class="brand">
      <span class="brand__mark"></span>
      <span class="brand__name">Quorvel Engineering Tandem</span>
    </div>
  </section>

  <section class="card card--back">
    <div class="brand">
      <span class="brand__mark"></span>
      <span class="brand__name">Quorvel Engineering Tandem</span>
    </div>

    <div class="identity">
      <p class="identity__name">Dorian Velasko</p>
      <p class="identity__role">Managing Director</p>
    </div>

    <span class="divider"></span>

    <ul class="contacts">
      <li class="contacts__item">
        <svg class="contacts__icon" viewBox="0 0 24 24" aria-hidden="true"><path fill="#e1bd24" d="M6.6 10.8a15.1 15.1 0 0 0 6.6 6.6l2.2-2.2a1 1 0 0 1 1-.25 11.4 11.4 0 0 0 3.6.57 1 1 0 0 1 1 1V20a1 1 0 0 1-1 1A17 17 0 0 1 3 4a1 1 0 0 1 1-1h3.5a1 1 0 0 1 1 1c0 1.25.2 2.45.57 3.57a1 1 0 0 1-.25 1z"/></svg>
        <span>(555)014-2387</span>
      </li>
      <li class="contacts__item">
        <svg class="contacts__icon" viewBox="0 0 24 24" aria-hidden="true"><path fill="#e1bd24" d="M2 5h20v14H2z"/><path fill="none" stroke="#fff" stroke-width="2" d="M2 6l10 7 10-7"/></svg>
        <span>hello@quorveltandem.com</span>
      </li>
      <li class="contacts__item">
        <svg class="contacts__icon" viewBox="0 0 24 24" aria-hidden="true"><circle cx="12" cy="12" r="10" fill="#e1bd24"/><path fill="none" stroke="#fff" stroke-width="1.6" d="M2 12h20M12 2c3 3 3 17 0 20M12 2c-3 3-3 17 0 20"/></svg>
        <span>www.quorveltandem.com</span>
      </li>
    </ul>
  </section>
</main>
</body>
</html>
```